My project benefits Military, First Responders, Police, Fire, and Educators.

Contact Information for Business Card

2 Sided appointment card. Visual side will have my head shot with "Brisk Lantern" in a bold graffic/text. I am picturing maybe the headshot applied to a filter that has a matrix effect where the picture is made up of data/numbers flowing vertically through the photo. I am of course open to other concepts as well. Side two will have contact info presented in an attractive visual complimenting the front.

```html
<!DOCTYPE html>
<html lang="en">
<head>
<meta charset="utf-8">
<title>Brisk Lantern – Business Card</title>
<link rel="stylesheet" href="https://fonts.googleapis.com/css2?family=Open+Sans:wght@300;400;700&display=swap">
<style>
  :root {
    --page-bg: #4a4340;
    --card-black: #0f0f10;
    --card-edge: #1c1c1e;
    --accent-blue: #1a8fd8;
    --text-light: #e6e6e6;
    --silver: #cfd0d2;
    --photo-dark: #1f2430;
    --photo-mid: #3b4660;
    --badge: #d9d9d9;
  }
  * { margin: 0; padding: 0; box-sizing: border-box; }
  html, body {
    width: 1200px; height: 900px; overflow: hidden;
    background: var(--page-bg);
    font-family: "Open Sans", Arial, sans-serif;
  }
  .canvas {
    position: relative; width: 1200px; height: 900px;
    display: flex; align-items: center; justify-content: center; gap: 40px;
  }
  .card {
    position: relative; width: 540px; height: 309px;
    background: var(--card-black);
    border: 1px solid var(--card-edge);
    box-shadow: 0 14px 30px rgba(0,0,0,0.45);
    overflow: hidden;
  }

  /* Contact side */
  .headshot {
    position: absolute; left: 40px; bottom: 0; width: 230px; height: 250px;
    background: radial-gradient(ellipse at 50% 35%, var(--photo-mid) 0%, var(--photo-dark) 60%, var(--card-black) 100%);
    border-radius: 110px 110px 0 0;
  }
  .contact {
    position: absolute; left: 292px; top: 52px; color: var(--text-light);
  }
  .contact-name {
    color: var(--accent-blue); font-weight: 700; font-size: 17px; letter-spacing: 0.3px;
    text-transform: uppercase; margin-bottom: 10px;
  }
  .contact-office { font-size: 12.5px; line-height: 1.4; margin-bottom: 12px; }
  .contact-line {
    display: flex; align-items: center; gap: 8px; font-size: 12.5px; margin-left: 30px; line-height: 1.55;
  }
  .contact-line svg { width: 10px; height: 10px; fill: var(--accent-blue); }
  .badges {
    position: absolute; left: 318px; top: 216px; display: flex; align-items: flex-end; gap: 24px;
  }
  .badge-house { width: 46px; height: 42px; }
  .badge-rect { width: 78px; height: 34px; border: 2px solid var(--badge); }

  /* Brand side */
  .brand {
    position: absolute; left: 0; right: 0; top: 62px;
    display: flex; flex-direction: column; align-items: center;
  }
  .brand-mark {
    width: 44px; height: 44px; border-radius: 50%; background: var(--silver);
    margin-bottom: 18px;
  }
  .brand-name {
    color: var(--silver); font-weight: 300; font-size: 38px; line-height: 1;
    letter-spacing: 1px; text-transform: uppercase;
  }
  .brand-sub {
    display: flex; align-items: center; gap: 10px; margin-top: 6px; width: 320px;
  }
  .brand-rule { flex: 1; height: 1px; background: var(--silver); }
  .brand-sub-text {
    color: var(--silver); font-weight: 300; font-size: 18px; line-height: 1; letter-spacing: 0.5px;
  }
</style>
</head>
<body>
<main class="canvas">
  <section class="card card-contact">
    <div class="headshot" role="img" aria-label="Headshot of Brisk Lantern in a dark suit and tie"></div>
    <div class="contact">
      <h1 class="contact-name">Brisk Lantern</h1>
      <p class="contact-office">Harlow Realty 4120 N.<br>57th Ave Glendale, AZ 85301</p>
      <p class="contact-line">
        <svg viewBox="0 0 10 10"><path d="M2 0 L4 2.5 L3 4 Q4.5 6 6 7 L7.5 6 L10 8 L8.5 10 Q3 9 0 1.5 Z"/></svg>
        555.014.2290
      </p>
      <p class="contact-line">
        <svg viewBox="0 0 10 10"><path d="M0 2 H10 V8 H0 Z M0 2 L5 5.5 L10 2" fill="var(--accent-blue)"/></svg>
        brisk@example.com
      </p>
    </div>
    <div class="badges">
      <svg class="badge-house" viewBox="0 0 46 42" aria-hidden="true">
        <path d="M4 20 L23 4 L42 20 V40 H4 Z" fill="none" stroke="var(--badge)" stroke-width="2.5"/>
      </svg>
      <div class="badge-rect" aria-hidden="true"></div>
    </div>
  </section>

  <section class="card card-brand">
    <div class="brand">
      <span class="brand-mark" aria-hidden="true"></span>
      <span class="brand-name">Brisk Lantern</span>
      <div class="brand-sub">
        <span class="brand-rule"></span>
        <span class="brand-sub-text">Group</span>
        <span class="brand-rule"></span>
      </div>
    </div>
  </section>
</main>
</body>
</html>
```